****Business Card Design for Quarrystone Development. Design based around attached logo/company name

I’m looking for business card design for my company Quarrystone Development Group,LLC. Design should be professional, sharp and minimal. Outside of the attached logos, greyscale colors for remainder of cards. My thoughts are two-sided card with attached logo on one side and my info on the other but open to one-sided as well with right design.
Target Market(s)
Real estate professionals including banks, private investors, property owners, developers, commercial tenants like Brewlantern, Grovika or Tanquist’s.
Industry/Entity Type
Commercial real estate development and investments.
Contact Information for Business Card
Name, title, email, phone #’s, web address and physical address
Font styles to use
Other font styles liked:
- Helvetica, Garamond, etc
Colors
Designer to choose only greyscale colors for use in the design.
Requirements
Must have
- Attached logo first or second options.
Nice to have
- Two sided card with logo on one side. Attached Logo/company name can be laid out any way that flows as long as it’s legible.name
Should not have
- No loud colors. ***Please do not include logo, I have removed the company design with a logo image.

```html
<!DOCTYPE html>
<html lang="en">
<head>
<meta charset="utf-8">
<title>Quarrystone Development Group, LLC — Business Card</title>
<link rel="stylesheet" href="https://fonts.googleapis.com/css2?family=EB+Garamond:wght@400&family=Arimo:wght@400&display=swap">
<style>
  :root {
    --backdrop: #2b2c2f;
    --card-top: #6f7a90;
    --card-bottom: #545c6e;
    --ink-dark: #1f2229;
    --ink-light: #f2f3f5;
    --ink-soft: #e3e6ec;
  }
  html, body {
    margin: 0;
    padding: 0;
    width: 1200px;
    height: 900px;
    overflow: hidden;
    background: var(--backdrop);
  }
  .canvas {
    position: relative;
    width: 1200px;
    height: 900px;
  }
  .card {
    position: absolute;
    left: 280px;
    width: 640px;
    height: 366px;
    background: linear-gradient(160deg, var(--card-top), var(--card-bottom));
    box-shadow: 0 14px 30px rgba(0,0,0,0.45);
  }
  .card--front { top: 64px; }
  .card--back { top: 470px; }

  .brand {
    position: absolute;
    left: 0;
    right: 0;
    top: 128px;
    display: flex;
    align-items: center;
    justify-content: center;
    gap: 18px;
  }
  .brand__mark {
    width: 16px;
    height: 16px;
    background: var(--ink-dark);
  }
  .brand__name {
    font-family: "EB Garamond", Georgia, serif;
    font-weight: 400;
    color: var(--ink-dark);
    text-transform: uppercase;
    line-height: 1.05;
  }
  .brand__primary {
    display: block;
    font-size: 50px;
    letter-spacing: 2px;
  }
  .brand__secondary {
    display: block;
    font-size: 21px;
    letter-spacing: 1.5px;
  }

  .contact {
    position: absolute;
    left: 54px;
    top: 52px;
    color: var(--ink-light);
    font-family: "Arimo", Helvetica, Arial, sans-serif;
  }
  .contact__name {
    margin: 0;
    font-family: "EB Garamond", Georgia, serif;
    font-weight: 400;
    font-size: 26px;
    letter-spacing: 1.5px;
    text-transform: uppercase;
  }
  .contact__title {
    margin: 2px 0 0;
    font-size: 15px;
    color: var(--ink-soft);
  }
  .contact__address {
    margin: 30px 0 0;
    font-style: normal;
    font-size: 16px;
    line-height: 1.3;
  }
  .contact__list {
    list-style: none;
    margin: 16px 0 0;
    padding: 0;
    font-size: 16px;
    line-height: 1.45;
  }
  .contact__item {
    display: flex;
    align-items: center;
    gap: 10px;
  }
  .contact__icon {
    width: 13px;
    height: 13px;
    fill: var(--ink-light);
    flex: none;
  }
</style>
</head>
<body>
<main class="canvas">

  <section class="card card--front" aria-label="Card front">
    <div class="brand">
      <span class="brand__mark" aria-hidden="true"></span>
      <p class="brand__name" style="margin:0">
        <span class="brand__primary">Quarrystone</span>
        <span class="brand__secondary">Development Group, LLC</span>
      </p>
    </div>
  </section>

  <section class="card card--back" aria-label="Card back">
    <div class="contact">
      <h1 class="contact__name">Daniel Harrow</h1>
      <p class="contact__title">President</p>
      <address class="contact__address">
        4120 Alder Crest Road<br>
        Juneau, Alaska 34588
      </address>
      <ul class="contact__list">
        <li class="contact__item">
          <svg class="contact__icon" viewBox="0 0 16 16" aria-hidden="true"><path d="M3.2 1.5l2.4-.4 1.6 3.6-1.5 1.2c.8 1.7 2 2.9 3.6 3.7l1.2-1.5 3.6 1.6-.4 2.4c-.2.9-1 1.5-1.9 1.4C6.6 12.9 3.1 9.4 2.6 4.2c-.1-.9.4-1.6 1.2-2.7z"/></svg>
          <span>555-218-4071</span>
        </li>
        <li class="contact__item">
          <svg class="contact__icon" viewBox="0 0 16 16" aria-hidden="true"><rect x="4" y="1" width="8" height="4"/><rect x="1" y="6" width="14" height="6" rx="1"/><rect x="4" y="10" width="8" height="5"/></svg>
          <span>555-326-9142</span>
        </li>
        <li class="contact__item">
          <svg class="contact__icon" viewBox="0 0 16 16" aria-hidden="true"><path d="M1 3h14v10H1z M1 3l7 6 7-6" fill="none" stroke="#f2f3f5" stroke-width="1.6"/></svg>
          <span>name@quarrystone.com</span>
        </li>
        <li class="contact__item">
          <svg class="contact__icon" viewBox="0 0 16 16" aria-hidden="true"><circle cx="8" cy="8" r="6.5" fill="none" stroke="#f2f3f5" stroke-width="1.4"/><path d="M1.5 8h13M8 1.5c-2.5 3-2.5 10 0 13M8 1.5c2.5 3 2.5 10 0 13" fill="none" stroke="#f2f3f5" stroke-width="1.2"/></svg>
          <span>www.quarrystone.com</span>
        </li>
      </ul>
    </div>
  </section>

</main>
</body>
</html>
```